I need a flyer made , the flyer can be one page or two pages or three pages . I will be posting this on Instagram and social media platforms. I am a luxury home builder , I am looking to hire a construction project manager . Below are some examples and ideas what can be on the flyer

We’re looking for a construction project manager who’s passionate about building luxury homes at the highest standards
We’re hiring construction project manager
* Experience 5+ years in residential project management with a strong portfolio of completed homes.
* location : Bergen County NJ
* excellent leadership skills, leads teams with confidence and clarity
* communicates seamlessly with architects , engineers, designers and clients
*knows how to manage budgets and timelines without compromising quality
*solves problems with a positive solution first mindset
* pays attention to every detail because in luxury the small things are the big things

Apply now , link in bio or DM to connect.

My logo is attached, my web site www.velstridebuilders.com
My style is modern but still warm and inviting. I like a clean classy look .

Please don’t add any images of chairs or people to the flyer , I do not want people on my flyer. Do not add standard images of offices and houses , we are luxury builders , we build homes over 2 million dollars. Keep a classy , simple modern look . High end .

You can add a white hard hat with my logo on it for a image , this is a suggestion does not have to be on my flyer ,

```html
<!DOCTYPE html>
<html lang="en">
<head>
<meta charset="utf-8">
<title>Velstride Builders – Hiring Construction Project Manager</title>
<link href="https://fonts.googleapis.com/css2?family=Poppins:wght@300;400;500;600;800&display=swap" rel="stylesheet">
<style>
  :root {
    --canvas: #cdd2da;
    --paper: #f1f2f2;
    --ink: #111111;
    --white: #ffffff;
    --muted: #6b6d70;
    --night-deep: #0d1a33;
    --night-blue: #1e3f74;
    --city-glow: #c98a3a;
  }
  * { box-sizing: border-box; margin: 0; padding: 0; }
  html, body {
    width: 1200px; height: 692px; overflow: hidden;
    background: var(--canvas);
    font-family: "Poppins", sans-serif;
  }
  .stage { position: relative; width: 1200px; height: 692px; }

  .page {
    position: absolute; top: 115px;
    width: 465px; height: 464px;
    background: var(--paper);
    overflow: hidden;
  }
  .page--cover { left: 119px; }
  .page--details { left: 596px; }

  /* cover page */
  .cover-photo {
    position: absolute; left: 0; top: 0; width: 465px; height: 425px;
    background:
      radial-gradient(ellipse 60% 40% at 75% 75%, rgba(201,138,58,.45), transparent 70%),
      radial-gradient(ellipse 50% 35% at 20% 80%, rgba(201,138,58,.3), transparent 70%),
      linear-gradient(180deg, #2b3346 0%, var(--night-blue) 35%, #163564 60%, var(--night-deep) 100%);
  }
  .cover-brandbar { position: absolute; left: 0; top: 0; width: 465px; height: 58px; }
  .brand {
    position: absolute; text-align: center;
    font-family: "Poppins", sans-serif; font-weight: 400;
    line-height: 1;
  }
  .brand__name { display: block; font-size: 27px; letter-spacing: 1px; }
  .brand__sub { display: block; font-size: 7px; letter-spacing: 1.6px; margin-top: 5px; }
  .brand--light { color: var(--white); left: 300px; top: 14px; width: 155px; }
  .brand--dark { color: var(--ink); left: 0; top: 18px; width: 465px; }

  .headline { position: absolute; left: 0; top: 0; color: var(--white); font-weight: 400; }
  .headline__lead {
    position: absolute; left: 53px; top: 223px;
    font-weight: 300; font-size: 41px; line-height: 1; letter-spacing: -1px; white-space: nowrap;
  }
  .headline__main {
    position: absolute; left: 52px; top: 256px;
    font-weight: 800; font-size: 61px; line-height: 1; letter-spacing: -1px; white-space: nowrap;
  }
  .headline__rule { position: absolute; left: 54px; top: 315px; width: 162px; height: 4px; background: var(--white); }

  .site-url {
    position: absolute; left: 0; top: 433px; width: 465px;
    text-align: center; font-weight: 300; font-size: 12.5px;
    letter-spacing: 3.2px; color: var(--muted);
  }

  /* details page */
  .intro {
    position: absolute; left: 18px; top: 84px;
    font-size: 13px; line-height: 15px; color: var(--ink);
  }
  .role-band {
    position: absolute; left: 0; top: 126px; width: 465px; height: 21px;
    background: linear-gradient(90deg, var(--ink) 0%, var(--ink) 60%, rgba(17,17,17,.55) 85%, rgba(17,17,17,0) 100%);
    color: var(--white); font-size: 13.4px; font-weight: 400; line-height: 21px; padding-left: 18px;
    white-space: nowrap;
  }
  .requirements { position: absolute; left: 0; top: 167px; width: 465px; list-style: none; }
  .requirements li {
    display: flex; align-items: center; height: 18.5px;
    font-size: 8.3px; color: var(--ink); white-space: nowrap;
  }
  .requirements svg { width: 26px; height: 8px; margin-right: 4px; flex: none; }

  .interior-render {
    position: absolute; left: 200px; top: 275px; width: 265px; height: 189px;
    background:
      linear-gradient(180deg, rgba(241,242,242,1) 0%, rgba(241,242,242,0) 35%),
      linear-gradient(90deg, rgba(241,242,242,1) 0%, rgba(241,242,242,0) 30%),
      linear-gradient(180deg, #dfe3e6 0%, #b9c4cc 45%, #a08a72 80%, #c49a6c 100%);
  }
  .cta { position: absolute; left: 0; top: 333px; width: 220px; height: 35px; }
  .cta__text { position: absolute; left: 18px; top: 340px; color: var(--white); line-height: 1.05; white-space: nowrap; }
  .cta__action { display: block; font-weight: 800; font-size: 11px; }
  .cta__note { display: block; font-size: 9.8px; }
</style>
</head>
<body>
<main class="stage">

  <section class="page page--cover">
    <div class="cover-photo" role="img" aria-label="Night city skyline seen through tall windows with a construction site and blueprint linework"></div>
    <svg class="cover-brandbar" viewBox="0 0 465 58" aria-hidden="true">
      <polygon points="285,0 465,0 465,58 247,58" fill="#111111"/>
      <polygon points="268,0 279,0 232,58 221,58" fill="#ffffff"/>
      <polygon points="283,0 294,0 247,58 236,58" fill="#ffffff"/>
      <polygon points="298,0 309,0 262,58 251,58" fill="#ffffff"/>
    </svg>
    <div class="brand brand--light">
      <span class="brand__name">VELSTRIDE</span>
      <span class="brand__sub">builders</span>
    </div>
    <h1 class="headline">
      <span class="headline__lead">WE’RE</span>
      <span class="headline__main">HIRING</span>
    </h1>
    <div class="headline__rule"></div>
    <p class="site-url">www.velstridebuilders.com</p>
  </section>

  <section class="page page--details">
    <div class="interior-render" role="img" aria-label="Sketch-to-render view of a luxury penthouse living room with city views"></div>

    <div class="brand brand--dark">
      <span class="brand__name">VELSTRIDE</span>
      <span class="brand__sub">builders</span>
    </div>
    <p class="intro">We’re looking for a construction project manager who’s passionate<br>about building luxury homes at the highest standards</p>
    <h2 class="role-band">WE’RE HIRING CONSTRUCTION PROJECT MANAGER</h2>

    <ul class="requirements">
      <li><svg viewBox="0 0 26 8"><polygon points="0,0 12,0 8,8 0,8" fill="#111"/><polygon points="14,0 16,0 12,8 10,8" fill="#111"/><polygon points="18,0 20,0 16,8 14,8" fill="#111"/><polygon points="22,0 24,0 20,8 18,8" fill="#111"/><polygon points="25,0 26,0 23,8 22,8" fill="#111"/></svg>Experience 5+ years in residential project management with a strong portfolio of completed homes</li>
      <li><svg viewBox="0 0 26 8"><polygon points="0,0 12,0 8,8 0,8" fill="#111"/><polygon points="14,0 16,0 12,8 10,8" fill="#111"/><polygon points="18,0 20,0 16,8 14,8" fill="#111"/><polygon points="22,0 24,0 20,8 18,8" fill="#111"/><polygon points="25,0 26,0 23,8 22,8" fill="#111"/></svg>Location : Bergen County NJ</li>
      <li><svg viewBox="0 0 26 8"><polygon points="0,0 12,0 8,8 0,8" fill="#111"/><polygon points="14,0 16,0 12,8 10,8" fill="#111"/><polygon points="18,0 20,0 16,8 14,8" fill="#111"/><polygon points="22,0 24,0 20,8 18,8" fill="#111"/><polygon points="25,0 26,0 23,8 22,8" fill="#111"/></svg>Excellent leadership skills, leads teams with confidence and clarity</li>
      <li><svg viewBox="0 0 26 8"><polygon points="0,0 12,0 8,8 0,8" fill="#111"/><polygon points="14,0 16,0 12,8 10,8" fill="#111"/><polygon points="18,0 20,0 16,8 14,8" fill="#111"/><polygon points="22,0 24,0 20,8 18,8" fill="#111"/><polygon points="25,0 26,0 23,8 22,8" fill="#111"/></svg>Communicates seamlessly with architects, engineers, designers and clients</li>
      <li><svg viewBox="0 0 26 8"><polygon points="0,0 12,0 8,8 0,8" fill="#111"/><polygon points="14,0 16,0 12,8 10,8" fill="#111"/><polygon points="18,0 20,0 16,8 14,8" fill="#111"/><polygon points="22,0 24,0 20,8 18,8" fill="#111"/><polygon points="25,0 26,0 23,8 22,8" fill="#111"/></svg>Knows how to manage budgets and timelines without compromising quality</li>
      <li><svg viewBox="0 0 26 8"><polygon points="0,0 12,0 8,8 0,8" fill="#111"/><polygon points="14,0 16,0 12,8 10,8" fill="#111"/><polygon points="18,0 20,0 16,8 14,8" fill="#111"/><polygon points="22,0 24,0 20,8 18,8" fill="#111"/><polygon points="25,0 26,0 23,8 22,8" fill="#111"/></svg>Solves problems with a positive solution first mindset</li>
      <li><svg viewBox="0 0 26 8"><polygon points="0,0 12,0 8,8 0,8" fill="#111"/><polygon points="14,0 16,0 12,8 10,8" fill="#111"/><polygon points="18,0 20,0 16,8 14,8" fill="#111"/><polygon points="22,0 24,0 20,8 18,8" fill="#111"/><polygon points="25,0 26,0 23,8 22,8" fill="#111"/></svg>Pays attention to every detail because in luxury the small things are the big things</li>
    </ul>

    <svg class="cta" viewBox="0 0 220 35" aria-hidden="true">
      <polygon points="0,0 185,0 220,35 0,35" fill="#111111"/>
    </svg>
    <p class="cta__text">
      <span class="cta__action">APPLY NOW,</span>
      <span class="cta__note">LINK IN BIO OR DM TO CONNECT</span>
    </p>

    <p class="site-url">www.velstridebuilders.com</p>
  </section>

</main>
</body>
</html>
```